Merrowin Vodka logo and label design

We would like a logo and bottle label design for a new line of Ultra-Premium Vodka. The Company is called Merrowin Spirits and is based in Brisbane, Australia. We would like a 'Gatsby/Prohibition era vibe to the design. We want to keep it minimalistic and sleek. We strongly prefer a minimalist design and colour palette. Black,Gold,Grey,White,Silver,Red and Blue

The bottle will be similar in shape to Castellane/Blue Heron. There will also need to be space on the label for required information, as well as short bio of the company, which will be provided to the winning design.
Updates

We would like to add the polish code of arms for Opoczno. Have attached link for reference. https://www.crestarchive-demo.net/crestwiki/index.php?title=Opoczno

Target Market(s)

Luxury brand customers

Logo Text

Merrowin Ultra-Premium Vodka

Logo styles of interest
Wordmark Logo
Lettermark Logo
Requirements
Must have
• This is the first release from our new Vodka label. We want a logo and bottle label that reflects a premium product. We very much like Prohibition/Gatsby era themed bottles and labels. The label and bottle should be elegant and clean.
Should not have
• Anything too busy or confusing.

```html
<!DOCTYPE html>
<html lang="en">
<head>
<meta charset="utf-8">
<title>Merrowin Ultra-Premium Vodka – Bottle Label</title>
<link rel="stylesheet" href="https://fonts.googleapis.com/css2?family=Cinzel:wght@400;500&family=Cormorant+Garamond:wght@500&display=swap">
<style>
  :root {
    --page: #ffffff;
    --ink-blue: #1d4fa6;
    --ink-blue-light: #2f66c4;
    --ink-blue-deep: #153f8c;
    --gold: #e2c16f;
    --gold-pale: #f4e2a6;
    --gold-deep: #b98d3c;
    --copper: #c9792f;
    --white: #ffffff;
    --rule-light: #d9e2f5;
  }
  * { margin: 0; padding: 0; box-sizing: border-box; }
  html, body {
    width: 877px;
    height: 1200px;
    overflow: hidden;
    background: var(--page);
  }
  .canvas {
    position: relative;
    width: 877px;
    height: 1200px;
    background: var(--page);
  }
  .label {
    position: absolute;
    left: 87px;
    top: 78px;
    width: 703px;
    height: 1004px;
    overflow: hidden;
    background:
      radial-gradient(ellipse at 30% 20%, var(--ink-blue-light) 0%, transparent 60%),
      radial-gradient(ellipse at 75% 80%, var(--ink-blue-light) 0%, transparent 55%),
      linear-gradient(160deg, var(--ink-blue) 0%, var(--ink-blue-deep) 100%);
  }
  .label-art {
    position: absolute;
    inset: 0;
    width: 100%;
    height: 100%;
  }
  .frame-line {
    fill: none;
    stroke: var(--gold);
    stroke-width: 1.6;
  }
  .medallion {
    fill: var(--ink-blue);
    stroke: var(--gold);
    stroke-width: 1.6;
  }
  .medallion-ring {
    fill: none;
    stroke: var(--gold);
    stroke-width: 1.6;
  }
  .rule-light {
    stroke: var(--rule-light);
    stroke-width: 0.7;
  }
  .medallion-name {
    font-family: "Cinzel", serif;
    font-size: 11px;
    font-weight: 500;
    letter-spacing: 1px;
    fill: var(--gold);
  }
  .text-block {
    position: absolute;
    left: 0;
    width: 100%;
    text-align: center;
    transform: translateY(-50%);
  }
  .wordmark {
    top: 369px;
    font-family: "Cinzel", serif;
    font-weight: 400;
    font-size: 54px;
    letter-spacing: 3px;
    color: var(--gold);
  }
  .product-line {
    top: 471px;
    font-family: "Cormorant Garamond", serif;
    font-weight: 500;
    font-variant: small-caps;
    font-size: 31px;
    letter-spacing: 0.5px;
    color: var(--gold-pale);
  }
  .origin {
    top: 640px;
    font-family: "Cormorant Garamond", serif;
    font-weight: 500;
    font-size: 22px;
    color: var(--white);
  }
  .origin .city { color: var(--copper); }
  .spec {
    position: absolute;
    top: 832px;
    transform: translate(-50%, -50%);
    font-family: "Cormorant Garamond", serif;
    font-weight: 500;
    font-size: 16px;
    color: var(--white);
    white-space: nowrap;
  }
  .spec-strength { left: 245px; }
  .spec-volume { left: 448px; }
</style>
</head>
<body>
<div class="canvas">
  <section class="label">
    <svg class="label-art" viewBox="0 0 393 577" preserveAspectRatio="xMidYMid meet" aria-hidden="false">
      <defs>
        <linearGradient id="fanGold" x1="0" y1="0" x2="1" y2="1">
          <stop offset="0" stop-color="#f4e2a6"/>
          <stop offset="1" stop-color="#b98d3c"/>
        </linearGradient>
      </defs>

      <!-- stepped side frames, left -->
      <path class="frame-line" d="M58 183 H28 V430 H74"/>
      <path class="frame-line" d="M60 200 H21 V437 H75"/>
      <path class="frame-line" d="M61 217 H14 V444 H76"/>
      <!-- stepped side frames, right -->
      <path class="frame-line" d="M335 183 H365 V430 H319"/>
      <path class="frame-line" d="M333 200 H372 V437 H318"/>
      <path class="frame-line" d="M332 217 H379 V444 H317"/>

      <!-- main tapered panel -->
      <path class="frame-line" d="M47 57 H346 L313 538 H80 Z" style="fill: var(--ink-blue)"/>
      <path class="frame-line" d="M55 65 H338 L306 530 H87 Z"/>

      <!-- side fan areas -->
      <path role="img" aria-label="Gold art deco fan ornament" d="M10 465 L10 395 Q50 405 78 465 Z" fill="url(#fanGold)" opacity="0.85"/>
      <path role="img" aria-label="Gold art deco fan ornament" d="M383 465 L383 395 Q343 405 315 465 Z" fill="url(#fanGold)" opacity="0.85"/>

      <!-- rules around product line -->
      <line class="frame-line" x1="112" y1="254" x2="272" y2="254"/>
      <line class="rule-light" x1="112" y1="257" x2="272" y2="257"/>
      <line class="frame-line" x1="112" y1="288" x2="272" y2="288"/>
      <line class="rule-light" x1="112" y1="291" x2="272" y2="291"/>

      <!-- top medallion with name -->
      <circle class="medallion" cx="196.5" cy="72" r="47"/>
      <circle class="medallion-ring" cx="196.5" cy="72" r="40"/>
      <text class="medallion-name" x="196.5" y="76" text-anchor="middle">MERROWIN</text>

      <!-- bottom medallion -->
      <circle class="medallion" cx="196.5" cy="525" r="37"/>
      <circle class="medallion-ring" cx="196.5" cy="525" r="31"/>
      <circle role="img" aria-label="Gold fan ornament" cx="196.5" cy="525" r="20" fill="url(#fanGold)" opacity="0.85"/>
    </svg>

    <h1 class="text-block wordmark">MERROWIN</h1>
    <p class="text-block product-line">Ultra-Premium Vodka</p>
    <p class="text-block origin"><span class="city">Brisbane</span>, Australia</p>
    <p class="spec spec-strength">40% alc./vol</p>
    <p class="spec spec-volume">700 ml</p>
  </section>
</div>
</body>
</html>
```